A-Stand Directional Sign Design

Objective:
We need a professional graphic design for an A-Stand sign that will guide customers arriving in our parking lot to our office. The design should be visually clear, welcoming, and aligned with our brand identity.
REQUIREMENTS:
Two versions of the design:
- One with an arrow pointing left
- One with an arrow pointing right
(This allows us to place the A-Stand anywhere and flip the graphic as needed.)
DIMENSIONS:
- Viewable Area: 30" x 40"
BRAND ALIGNMENT:
- Colors, fonts, and overall style should match our website: www.glidemarrow.com
- Clean, modern, and professional look consistent with our aviation/tourism brand
CONTENT:
- Clear directional arrow (left or right depending on version)
- Text: “Office Entrance” or similar concise wording (designers may propose alternatives if they improve clarity)
READABILITY:
- Bold, high-contrast design for visibility from a distance
- Simple layout that avoids clutter
DELIVERABLES:
- Final artwork in print-ready format (PDF preferred)
- Two versions: Arrow Left and Arrow Right
DESIGN GOAL:
Ensure customers can easily find our office upon arrival, while reinforcing glideMARROW’s professional and welcoming brand image.
Target Market(s)
Tourism
Look and feel

```html
<!DOCTYPE html>
<html lang="en">
<head>
<meta charset="utf-8">
<title>glideMARROW – Office Entrance A-Stand Signs</title>
<link rel="stylesheet" href="https://fonts.googleapis.com/css2?family=Anton&family=Montserrat:wght@600&display=swap">
<style>
  :root {
    --page-bg: #f3f4f5;
    --sign-blue: #1f78b9;
    --arrow-blue: #86aad7;
    --ink-white: #ffffff;
  }
  * { box-sizing: border-box; margin: 0; padding: 0; }
  html, body {
    width: 1200px;
    height: 929px;
    overflow: hidden;
    background: var(--page-bg);
  }
  .sign-set {
    position: relative;
    width: 1200px;
    height: 929px;
    display: flex;
    justify-content: center;
    align-items: center;
    gap: 50px;
  }
  .sign-panel {
    position: relative;
    width: 540px;
    height: 720px;
    background: var(--sign-blue);
    overflow: hidden;
  }
  .brand-lockup {
    position: absolute;
    top: 72px;
    left: 0;
    right: 0;
    display: flex;
    justify-content: center;
    align-items: center;
    gap: 12px;
  }
  .brand-dot {
    width: 22px;
    height: 22px;
    border-radius: 50%;
    background: var(--ink-white);
  }
  .brand-name {
    font-family: "Montserrat", sans-serif;
    font-weight: 600;
    font-size: 32px;
    letter-spacing: 0.5px;
    color: var(--ink-white);
  }
  .sign-heading {
    position: absolute;
    top: 185px;
    left: 0;
    right: 0;
    text-align: center;
    font-family: "Anton", sans-serif;
    font-weight: 400;
    font-size: 104px;
    line-height: 1;
    color: var(--ink-white);
    text-transform: uppercase;
  }
  .direction-arrow {
    position: absolute;
    left: 0;
    top: 0;
    width: 540px;
    height: 720px;
  }
  .direction-arrow path {
    fill: none;
    stroke: var(--arrow-blue);
    stroke-width: 36;
    stroke-linejoin: round;
  }
  .direction-arrow .arrow-head { stroke-linecap: round; }
</style>
</head>
<body>
  <main class="sign-set">
    <section class="sign-panel sign-panel--right" aria-label="Office entrance sign, arrow right">
      <div class="brand-lockup">
        <span class="brand-dot"></span>
        <span class="brand-name">glideMARROW</span>
      </div>
      <h1 class="sign-heading">Office<br>Entrance</h1>
      <svg class="direction-arrow" viewBox="0 0 540 720" aria-hidden="true">
        <path d="M150 740 V535 H420"/>
        <path class="arrow-head" d="M335 450 L420 535 L335 620"/>
      </svg>
    </section>

    <section class="sign-panel sign-panel--left" aria-label="Office entrance sign, arrow left">
      <div class="brand-lockup">
        <span class="brand-dot"></span>
        <span class="brand-name">glideMARROW</span>
      </div>
      <h1 class="sign-heading">Office<br>Entrance</h1>
      <svg class="direction-arrow" viewBox="0 0 540 720" aria-hidden="true">
        <path d="M420 740 V535 H120"/>
        <path class="arrow-head" d="M205 450 L120 535 L205 620"/>
      </svg>
    </section>
  </main>
</body>
</html>
```